Billboard design for dentist that sees only children

I own a 12' x 25' digital billboard and I need help with billboard design. My wife is a general dentist that only sees children and is very passionate about giving them a quality dental experience . She has a great reputation in town. Obviously with a billboard there can't be a lot of reading. Maybe something that shows safety, love, experience and children. I am completely open to your ideas. In addition I have other businesses that also need billboard design so this could lead to more work. If you go to Maplecovedental.com under the about section you will find more information about the practice and our phone number. Attached is our logo which could be changed and content specs for the digital billboard. Happy Designing!!

Target Market(s)

Parents with children

Colors

Designer to choose colors to be used in the design.

Requirements
Must have
• Must attract attention and be nice to look at.
Nice to have
• Probably should have children in the picture ..... Maybe
Should not have
• If I see something I don't like I will let you know

```html
<!DOCTYPE html>
<html lang="en">
<head>
<meta charset="utf-8">
<title>Maple Cove Dental – Billboard</title>
<link href="https://fonts.googleapis.com/css2?family=Fredoka:wght@500;600&family=Patrick+Hand&family=Oswald:wght@500&family=Open+Sans:ital,wght@1,700&display=swap" rel="stylesheet">
<style>
  :root {
    --frame-blue: #4a72b8;
    --brand-green: #2e7d5b;
    --headline-orange: #f08a30;
    --headline-pink: #e8386a;
    --tagline-navy: #2b4763;
    --phone-brown: #4a2e24;
    --web-teal: #4aa6b0;
    --paper: #ffffff;
  }
  html, body {
    margin: 0;
    padding: 0;
    width: 1200px;
    height: 576px;
    overflow: hidden;
    background: var(--paper);
  }
  .billboard {
    position: relative;
    width: 1200px;
    height: 576px;
    background: var(--paper);
    overflow: hidden;
    font-family: "Fredoka", sans-serif;
  }
  .hero-photo {
    position: absolute;
    left: 592px;
    top: 0;
    width: 608px;
    height: 576px;
    background:
      radial-gradient(ellipse 38% 45% at 40% 40%, rgba(240, 200, 180, 0.85), rgba(240, 200, 180, 0) 100%),
      radial-gradient(ellipse 30% 40% at 78% 38%, rgba(232, 190, 165, 0.85), rgba(232, 190, 165, 0) 100%),
      radial-gradient(ellipse 45% 35% at 75% 85%, rgba(190, 198, 210, 0.8), rgba(190, 198, 210, 0) 100%),
      linear-gradient(90deg, #ffffff 0%, #eef5f3 25%, #e6efee 100%);
  }
  .frame {
    position: absolute;
    left: 0;
    top: 0;
    width: 1200px;
    height: 576px;
  }
  .brand {
    position: absolute;
    left: 142px;
    top: 66px;
    display: flex;
    align-items: center;
    gap: 14px;
  }
  .brand-dot {
    width: 60px;
    height: 60px;
    border-radius: 50%;
    background: var(--frame-blue);
  }
  .brand-name {
    font-family: "Fredoka", sans-serif;
    font-weight: 500;
    font-size: 38px;
    color: var(--brand-green);
    line-height: 1;
  }
  .headline-top {
    position: absolute;
    left: 0;
    width: 694px;
    text-align: center;
    top: 180px;
    margin: 0;
    font-family: "Fredoka", sans-serif;
    font-weight: 600;
    font-size: 44px;
    line-height: 43px;
    letter-spacing: 1px;
    color: var(--headline-orange);
  }
  .headline-arc {
    position: absolute;
    left: 0;
    top: 0;
    width: 700px;
    height: 420px;
  }
  .headline-arc .smiles {
    font-family: "Fredoka", sans-serif;
    font-weight: 600;
    font-size: 62px;
    fill: var(--headline-pink);
  }
  .headline-arc .tagline {
    font-family: "Patrick Hand", sans-serif;
    font-size: 21px;
    fill: var(--tagline-navy);
  }
  .contact {
    position: absolute;
    left: 160px;
    top: 446px;
  }
  .call-line {
    margin: 0;
    font-family: "Oswald", sans-serif;
    font-weight: 500;
    font-size: 30px;
    line-height: 40px;
  }
  .call-prompt { color: var(--headline-orange); }
  .call-number { color: var(--phone-brown); }
  .web-line {
    margin: 0;
    font-family: "Open Sans", sans-serif;
    font-style: italic;
    font-weight: 700;
    font-size: 24px;
    line-height: 36px;
    color: var(--web-teal);
  }
</style>
</head>
<body>
  <main class="billboard">
    <div class="hero-photo" role="img" aria-label="Photo of a smiling mother holding her laughing toddler cheek to cheek"></div>

    <svg class="frame" viewBox="0 0 1200 576" aria-hidden="true">
      <defs>
        <linearGradient id="frame-top-fade" x1="0" y1="0" x2="1" y2="0">
          <stop offset="0.72" stop-color="#4a72b8"/>
          <stop offset="1" stop-color="#4a72b8" stop-opacity="0"/>
        </linearGradient>
        <linearGradient id="frame-bottom-fade" x1="0" y1="0" x2="1" y2="0">
          <stop offset="0.75" stop-color="#4a72b8"/>
          <stop offset="1" stop-color="#4a72b8" stop-opacity="0"/>
        </linearGradient>
      </defs>
      <rect x="35" y="32" width="670" height="5" fill="url(#frame-top-fade)"/>
      <rect x="35" y="32" width="5" height="512" fill="#4a72b8"/>
      <rect x="35" y="539" width="740" height="5" fill="url(#frame-bottom-fade)"/>
    </svg>

    <div class="brand">
      <span class="brand-dot"></span>
      <span class="brand-name">Maple Cove Dental</span>
    </div>

    <h1 class="headline-top">ENHANCE<br>THEIR</h1>

    <svg class="headline-arc" viewBox="0 0 700 420" aria-label="Happy Smiles – General dentistry for children">
      <defs>
        <path id="smile-curve" d="M110 292 Q350 382 590 286"/>
        <path id="tagline-curve" d="M194 352 Q352 386 518 346"/>
      </defs>
      <text class="smiles"><textPath href="#smile-curve" startOffset="50%" text-anchor="middle">HAPPY SMILES</textPath></text>
      <text class="tagline"><textPath href="#tagline-curve" startOffset="50%" text-anchor="middle">General dentistry for children</textPath></text>
    </svg>

    <div class="contact">
      <p class="call-line"><span class="call-prompt">Call Us Today!</span> <span class="call-number">555 014 2368</span></p>
      <p class="web-line">www.maplecovedental.com</p>
    </div>
  </main>
</body>
</html>
```